Business Card Design for Marketing Firm

Looking for business card design for higher end marketing firm. Clean but impressionable/trendy. We are a marketing firm that represents manufacturers in the foodservice equipment and supply industry. Our customers are end users such has hotels, restaurants, country clubs, convention centers and casinos as well as distributors of restaurants supplies and equipment, and manufacturers of foodservice equipment and supplies.
Target Market(s)
Hotels, Restaurants, Supply & Equipment Distributors, Foodservice Manufacturers
Industry/Entity Type
Foodservice/Hospitality
Contact Information for Business Card
Name, Title, Contact Number, Email, Website, Social Media, Address
Requirements
Must have
- Clean & Simple but Serious and Impressionable

```html
<!DOCTYPE html>
<html lang="en">
<head>
<meta charset="utf-8">
<title>Meridian Hospitality Reps — Business Card</title>
<link href="https://fonts.googleapis.com/css2?family=Cinzel:wght@500&family=EB+Garamond:wght@400;500&display=swap" rel="stylesheet">
<style>
  :root {
    --navy: #262b7c;
    --navy-faint: #e4e5ef;
    --card: #ffffff;
    --card-edge: #f1f1f3;
    --backdrop: #e2e2e5;
    --ink-soft: #4a4d6a;
  }
  * { box-sizing: border-box; margin: 0; padding: 0; }
  html, body { width: 1200px; height: 900px; overflow: hidden; }
  body {
    background: var(--backdrop);
    font-family: "EB Garamond", Georgia, serif;
    color: var(--navy);
    position: relative;
  }
  .card {
    position: absolute;
    left: 290px;
    width: 620px;
    height: 354px;
    border-radius: 38px;
    background: linear-gradient(135deg, var(--card-edge), var(--card) 60%);
    box-shadow: 0 6px 18px rgba(0,0,0,0.12);
    overflow: hidden;
  }
  .card--front { top: 70px; }
  .card--back { top: 476px; }

  .lockup { position: absolute; text-align: left; }
  .lockup__mark {
    font-family: "Cinzel", "Times New Roman", serif;
    font-weight: 500;
    color: var(--navy);
    display: flex;
    align-items: center;
    gap: 10px;
  }
  .lockup__dot {
    width: 16px; height: 16px; border-radius: 50%;
    background: var(--navy);
    flex: none;
  }
  .lockup__name {
    font-family: "Cinzel", "Times New Roman", serif;
    font-weight: 500;
    color: var(--navy);
    white-space: nowrap;
    line-height: 1;
  }
  .lockup__reps {
    font-family: "Cinzel", "Times New Roman", serif;
    font-weight: 500;
    color: var(--navy);
    text-align: right;
    line-height: 1;
  }
  .lockup__rule { height: 2px; background: var(--navy); }

  /* front */
  .card--front .lockup { left: 50%; top: 112px; transform: translateX(-50%); width: 340px; }
  .card--front .lockup__mark { font-size: 30px; justify-content: center; margin-bottom: 20px; }
  .card--front .lockup__name { font-size: 27px; letter-spacing: 1px; }
  .card--front .lockup__reps { font-size: 15px; margin-top: 2px; }
  .card--front .lockup__rule { margin-top: 6px; width: 88%; }

  .social { position: absolute; left: 50%; top: 268px; transform: translateX(-50%); display: flex; gap: 10px; }
  .social__dot { width: 18px; height: 18px; border-radius: 50%; background: var(--navy); }

  /* back */
  .card--back .lockup { left: 52px; top: 70px; width: 300px; }
  .card--back .lockup__mark { font-size: 26px; margin-bottom: 16px; }
  .card--back .lockup__name { font-size: 24px; letter-spacing: 1px; }
  .card--back .lockup__reps { font-size: 13px; margin-top: 2px; }
  .card--back .lockup__rule { margin-top: 6px; width: 88%; }

  .backdrop-word {
    position: absolute; right: -10px; top: 14px;
    font-family: "Cinzel", "Times New Roman", serif;
    font-size: 96px; font-weight: 500;
    color: var(--navy-faint);
    line-height: 1;
  }

  .person { position: absolute; right: 268px; bottom: 60px; text-align: right; }
  .person__title { font-size: 17px; color: var(--ink-soft); }
  .person__name {
    font-family: "Cinzel", "Times New Roman", serif;
    font-size: 20px; font-weight: 500; letter-spacing: 0.5px;
  }
  .divider { position: absolute; right: 252px; bottom: 52px; width: 1.5px; height: 96px; background: var(--navy); }

  .contact { position: absolute; left: 382px; bottom: 56px; list-style: none; }
  .contact__item { display: flex; align-items: center; gap: 8px; font-size: 15px; line-height: 23px; color: var(--ink-soft); white-space: nowrap; }
  .contact__icon { width: 13px; height: 13px; flex: none; fill: var(--navy); }
</style>
</head>
<body>

<section class="card card--front">
  <div class="lockup">
    <div class="lockup__mark"><span class="lockup__dot"></span>Meridian</div>
    <div class="lockup__name">Meridian Hospitality</div>
    <div class="lockup__reps">Reps</div>
    <div class="lockup__rule"></div>
  </div>
  <div class="social">
    <span class="social__dot"></span><span class="social__dot"></span><span class="social__dot"></span>
  </div>
</section>

<section class="card card--back">
  <div class="backdrop-word">Meridian</div>
  <div class="lockup">
    <div class="lockup__mark"><span class="lockup__dot"></span>Meridian</div>
    <div class="lockup__name">Meridian Hospitality</div>
    <div class="lockup__reps">Reps</div>
    <div class="lockup__rule"></div>
  </div>

  <div class="person">
    <div class="person__title">Director</div>
    <div class="person__name">DANIEL REYES</div>
  </div>
  <div class="divider"></div>

  <ul class="contact">
    <li class="contact__item">
      <svg class="contact__icon" viewBox="0 0 16 16"><path d="M3.5 1h3l1.5 4-2 1.3a9 9 0 0 0 3.7 3.7L11 8l4 1.5v3A2 2 0 0 1 13 15 12 12 0 0 1 1 3a2 2 0 0 1 2.5-2z"/></svg>
      310-4200-7100
    </li>
    <li class="contact__item">
      <svg class="contact__icon" viewBox="0 0 16 16"><path d="M1 3h14v10H1z M1.5 3.5 8 9l6.5-5.5" fill="none" stroke="#262b7c" stroke-width="1.6"/></svg>
      info@meridianhospitalityreps.com
    </li>
    <li class="contact__item">
      <svg class="contact__icon" viewBox="0 0 16 16"><g fill="none" stroke="#262b7c" stroke-width="1.3"><circle cx="8" cy="8" r="6.5"/><ellipse cx="8" cy="8" rx="3" ry="6.5"/><path d="M1.5 8h13M2.5 4.8h11M2.5 11.2h11"/></g></svg>
      www.meridianhospitalityreps.com
    </li>
    <li class="contact__item">
      <svg class="contact__icon" viewBox="0 0 16 16"><path d="M8 1a5 5 0 0 1 5 5c0 4-5 9-5 9S3 10 3 6a5 5 0 0 1 5-5zm0 3a2 2 0 1 0 0 4 2 2 0 0 0 0-4z"/></svg>
      Austin, Texas
    </li>
  </ul>
</section>

</body>
</html>
```